Card design for orthopaedic surgeons working as The Brightwater Joint Centre

Business cards, letterhead

Colors

Designer to choose colors to be used in the design.

Requirements
Must have
• Late addition.
• Cards letterhead must have logos of
• Crestmoor Lindell College of Surgeons
• Varenwood Bone Health Association
Nice to have
• Back of card to have space for appointment time to be added by hand and some blank space for writing incidental other notes.

```html
<!DOCTYPE html>
<html lang="en">
<head>
<meta charset="utf-8">
<title>The Brightwater Joint Centre – Business Cards</title>
<link href="https://fonts.googleapis.com/css2?family=Montserrat:wght@400&family=Open+Sans:wght@400;700&display=swap" rel="stylesheet">
<style>
  :root {
    --backdrop: #1f2022;
    --card: #ffffff;
    --navy: #0a3650;
    --sky: #35aff9;
    --ink: #1c2a36;
    --on-sky: #ffffff;
  }
  * { box-sizing: border-box; margin: 0; padding: 0; }
  html, body {
    width: 1200px; height: 960px; overflow: hidden;
    background: var(--backdrop);
  }
  .canvas { position: relative; width: 1200px; height: 960px; }

  .card {
    position: absolute;
    width: 560px; height: 320px;
    background: var(--card);
    overflow: hidden;
    box-shadow: 0 10px 30px rgba(0,0,0,.45);
  }

  /* Brand wordmark: one colour, one weight */
  .wordmark {
    font-family: "Montserrat", sans-serif;
    font-weight: 400;
    color: var(--navy);
    letter-spacing: -0.5px;
    white-space: nowrap;
  }

  /* Back of card */
  .card--back { left: 560px; top: 130px; }
  .card--back .wordmark {
    position: absolute; left: 0; right: 0; top: 118px;
    text-align: center; font-size: 34px;
  }
  .card--back .web-address {
    position: absolute; left: 0; right: 0; top: 200px;
    text-align: center;
    font-family: "Open Sans", sans-serif; font-size: 16px;
    letter-spacing: 4px; color: var(--ink);
  }
  .web-address .domain { color: var(--sky); }

  /* Front of card */
  .card--front { left: 80px; top: 500px; }
  .card--front .wordmark {
    position: absolute; left: 30px; top: 34px; font-size: 26px;
  }
  .holder { position: absolute; left: 34px; top: 104px; font-family: "Open Sans", sans-serif; }
  .holder-name { font-weight: 700; font-size: 19px; color: var(--navy); line-height: 1.1; }
  .holder-title { font-size: 14px; color: var(--sky); }

  .contact-band {
    position: absolute; left: 0; bottom: 0;
    width: 405px; height: 166px;
    background: var(--sky);
    border-top-right-radius: 26px;
    padding: 16px 0 0 34px;
    font-family: "Open Sans", sans-serif; font-size: 14px;
    color: var(--on-sky); list-style: none;
  }
  .contact-band li { display: flex; align-items: center; gap: 9px; height: 23px; }
  .contact-band svg { width: 13px; height: 13px; flex: none; }
  .contact-band .address { margin-top: 8px; font-size: 15px; }

  .accent-block {
    position: absolute; right: 0; bottom: 0;
    width: 140px; height: 98px;
    background: var(--navy);
    border-top-left-radius: 18px;
  }
</style>
</head>
<body>
<main class="canvas">

  <section class="card card--back" aria-label="Card back">
    <div class="wordmark">The Brightwater Joint Centre</div>
    <p class="web-address">www.<span class="domain">brightwaterjoint</span>.com</p>
  </section>

  <section class="card card--front" aria-label="Card front">
    <div class="wordmark">The Brightwater Joint Centre</div>
    <div class="holder">
      <p class="holder-name">Maren Holloway</p>
      <p class="holder-title">Title</p>
    </div>
    <ul class="contact-band">
      <li>
        <svg viewBox="0 0 16 16" aria-hidden="true"><path fill="currentColor" d="M3.5 1.5l2.5 0 1 3.5-1.6 1.2a9 9 0 0 0 4.4 4.4L11 9l3.5 1v2.5c0 1-1 2-2 2A11 11 0 0 1 1.5 3.5c0-1 1-2 2-2z"/></svg>
        012-345-6789
      </li>
      <li>
        <svg viewBox="0 0 16 16" aria-hidden="true"><rect x="1" y="3" width="14" height="10" rx="1.5" fill="currentColor"/><path d="M1.5 4l6.5 5 6.5-5" stroke="#35aff9" stroke-width="1.4" fill="none"/></svg>
        info@brightwaterjoint.com
      </li>
      <li>
        <svg viewBox="0 0 16 16" aria-hidden="true"><circle cx="8" cy="8" r="6.5" fill="none" stroke="currentColor" stroke-width="1.4"/><path d="M1.5 8h13M8 1.5c-3 3.5-3 9.5 0 13M8 1.5c3 3.5 3 9.5 0 13" fill="none" stroke="currentColor" stroke-width="1.2"/></svg>
        www.brightwaterjoint.com
      </li>
      <li class="address">Street Name, City Name, Zipcode - 012345</li>
    </ul>
    <div class="accent-block"></div>
  </section>

</main>
</body>
</html>
```